Recruitment Site Design

We need a design for the login page, about page, and inner pages of a recruitment site for an oil and gas company. Design should be modern, sleek, professional and colors can be blue, green, white, orange or any other recommended colors.

Please also take into consideration that once the users login, they will need to access a form to fill in their information.

** UPDATE: Kindly provide a design for the inner information page consistent with the outer design. Attached is a picture of the basic structure. ***
Updates

Please provide a design for inner pages as shown in the design brief consistent with the registration page provided. 

Reason: We're extending it to get more inside pages.

Target Market(s)

Professionals looking for a career in the oil and gas industry in the Middle East.

Industry/Entity Type

Oil And Gas

Requirements
Must have
• Sleek design

```html
<!DOCTYPE html>
<html lang="en">
<head>
<meta charset="utf-8">
<title>Recruitment – Home</title>
<link href="https://fonts.googleapis.com/css2?family=Open+Sans:wght@400;600&family=PT+Sans:wght@400;700&family=PT+Sans+Narrow:wght@400;700&family=Merienda:wght@700&display=swap" rel="stylesheet">
<style>
:root{
  --page:#e9ecef;
  --blue:#1f7fd0;
  --blue-dark:#0b4a8c;
  --blue-deep:#083c74;
  --blue-light:#5aa9ea;
  --heading:#1a6cb5;
  --text:#3b3b3b;
  --rule:#b9bcbf;
  --white:#ffffff;
}
*{margin:0;padding:0;box-sizing:border-box}
html,body{width:1039px;height:1200px;overflow:hidden;background:var(--page)}
body{font-family:"PT Sans",sans-serif;color:var(--text)}
.canvas{position:relative;width:1039px;height:1200px;overflow:hidden;background:var(--page)}
.abs{position:absolute}
.hero-photo{left:0;top:60px;width:1039px;height:500px;
  background:linear-gradient(180deg,#4f7fbf 0%,#7ea6d6 45%,#c9d9ea 80%,#a9b78a 100%)}
.shapes{left:0;top:0;width:1039px;height:1200px}
.logo{left:132px;top:62px;font-family:"Open Sans",sans-serif;font-weight:600;font-size:72px;color:#8fa9c4;letter-spacing:1px}
.social{left:852px;top:45px;display:flex;gap:8px}
.social span{width:26px;height:26px;border-radius:5px;background:var(--blue);display:block}
.tagline{left:94px;top:330px;font-family:"Merienda",cursive;font-size:23px;line-height:32px;color:var(--white);text-shadow:1px 2px 3px rgba(0,0,0,.6)}
.dots{left:192px;top:468px;width:92px;height:40px;border-radius:12px 12px 0 0;background:#e4e6e8;display:flex;justify-content:center;gap:7px;padding-top:12px}
.dots i{width:12px;height:12px;border-radius:50%;background:#9a9a9a;display:block}
.dots i.on{background:var(--blue)}
.nav{left:71px;top:558px;width:713px;height:64px;display:flex}
.nav a{font-family:"Open Sans",sans-serif;font-size:15px;color:var(--white);text-decoration:none;display:flex;align-items:center;justify-content:center;height:100%}
.nav a.active{color:#0d2d55;font-weight:600}
.section-title{font-family:"Open Sans",sans-serif;font-size:18px;color:var(--heading);font-weight:400}
.rule{height:2px;background:var(--rule)}
.welcome-title{left:87px;top:662px}
.welcome-rule{left:83px;top:690px;width:644px}
.portrait{left:86px;top:708px;width:78px;height:93px;border:2px solid #9eb3c8;background:linear-gradient(160deg,#2a3446,#4a5468 55%,#c79a6e 100%)}
.intro{left:180px;top:703px;width:545px;font-size:14px;line-height:22.6px;text-align:justify}
.theory-title{left:180px;top:803px;font-size:14px;color:var(--heading);font-weight:400;letter-spacing:.3px}
.theory-list{left:190px;top:825px;list-style:none;font-size:14px;line-height:21px}
.theory-list li{display:flex;align-items:center;gap:6px}
.theory-list svg{width:14px;height:12px}
.history-title{left:86px;top:896px}
.history-rule{left:83px;top:925px;width:644px}
.carousel{left:84px;top:941px;width:642px;height:128px}
.carousel-photo{top:954px;width:130px;height:103px;border:2px solid #9cc3e8}
.p1{left:129px;background:linear-gradient(140deg,#6a7a70,#d9a582 50%,#efe3d6)}
.p2{left:268px;background:linear-gradient(140deg,#34507a,#e8e6e2 50%,#8aa6c8)}
.p3{left:410px;background:linear-gradient(140deg,#6a7a70,#d9a582 50%,#efe3d6)}
.p4{left:548px;background:linear-gradient(140deg,#34507a,#e8e6e2 50%,#8aa6c8)}
.login{left:752px;top:675px;width:225px;height:200px}
.login-title{left:786px;top:688px;width:158px;text-align:center;font-family:"Open Sans",sans-serif;font-size:19px;color:var(--white)}
.field{left:772px;width:182px;height:35px;background:var(--white);border:1px solid #9fb6cc;border-radius:4px;font-size:12.5px;color:#555;padding:0 9px;display:flex;align-items:center}
.f1{top:741px}.f2{top:785px}
.btn{top:830px;height:28px;border-radius:3px;background:linear-gradient(180deg,#3a97e4,#1566b4);color:var(--white);font-size:13px;display:flex;align-items:center;justify-content:center;border:1px solid #5eaaf0}
.b1{left:774px;width:66px}.b2{left:851px;width:102px}
.address-title{left:756px;top:894px;font-family:"PT Sans Narrow",sans-serif;font-weight:700;font-size:21px;color:var(--heading)}
.address-rule{left:756px;top:925px;width:221px}
.address{left:756px;top:938px;font-size:14px;line-height:21.4px;font-family:"PT Sans Narrow",sans-serif;font-size:15px}
.copyright{left:89px;top:1168px;font-size:12px;color:var(--white)}
.copyright u{text-decoration:underline}
.footer-nav{left:623px;top:1168px;font-size:12px;color:var(--white);display:flex;gap:11px}
</style>
</head>
<body>
<div class="canvas">
  <div class="abs hero-photo" role="img" aria-label="Photo: oil pump jacks under a cloudy sky with an engineer in orange coveralls and hard hat holding a laptop"></div>

  <svg class="abs shapes" viewBox="0 0 1039 1200" aria-hidden="true">
    <defs>
      <linearGradient id="headerFill" x1="0" y1="0" x2="0" y2="1">
        <stop offset="0" stop-color="#eef1f4"/><stop offset=".6" stop-color="#c9d9ea"/><stop offset="1" stop-color="#6fa0d2"/>
      </linearGradient>
      <linearGradient id="navFill" x1="0" y1="0" x2="0" y2="1">
        <stop offset="0" stop-color="#0d5aa6"/><stop offset="1" stop-color="#2a8ae0"/>
      </linearGradient>
      <linearGradient id="loginFill" x1="0" y1="0" x2="0" y2="1">
        <stop offset="0" stop-color="#0a4b90"/><stop offset="1" stop-color="#073f7a"/>
      </linearGradient>
      <linearGradient id="tabFill" x1="0" y1="0" x2="0" y2="1">
        <stop offset="0" stop-color="#3a98e6"/><stop offset="1" stop-color="#0a4b90"/>
      </linearGradient>
      <linearGradient id="footerFill" x1="0" y1="0" x2="0" y2="1">
        <stop offset="0" stop-color="#3192e2"/><stop offset=".45" stop-color="#155fae"/><stop offset="1" stop-color="#0a4586"/>
      </linearGradient>
    </defs>
    <!-- header band -->
    <path d="M0,0 H1039 V108 C900,98 760,118 600,140 C430,164 260,172 0,150 Z" fill="url(#headerFill)"/>
    <path d="M0,150 C260,172 430,164 600,140 C760,118 900,98 1039,108" fill="none" stroke="#4f9be0" stroke-width="3"/>
    <!-- hero bottom edge -->
    <path d="M0,528 C150,515 280,503 420,506 C600,510 800,545 1039,555 V570 H0 Z" fill="var(--page)"/>
    <path d="M0,528 C150,515 280,503 420,506 C600,510 800,545 1039,555" fill="none" stroke="#6fb0ea" stroke-width="2"/>
    <!-- nav -->
    <path d="M71,518 C180,510 300,504 420,506 C560,509 680,526 784,543 V612 Q784,623 773,623 H82 Q71,623 71,612 Z" fill="url(#navFill)"/>
    <g stroke="#5fa6e6" stroke-width="1.5">
      <line x1="202" y1="557" x2="202" y2="622"/><line x1="339" y1="557" x2="339" y2="622"/>
      <line x1="471" y1="557" x2="471" y2="622"/><line x1="638" y1="557" x2="638" y2="622"/>
    </g>
    <!-- login panel -->
    <rect x="752" y="686" width="225" height="189" rx="7" fill="url(#loginFill)" stroke="#5d96cf" stroke-width="1"/>
    <path d="M778,676 H949 L956,684 V726 H786 V684 Z" fill="url(#tabFill)"/>
    <!-- carousel frame -->
    <rect x="84" y="941" width="642" height="128" rx="4" fill="#2676c6"/>
    <rect x="114" y="944" width="582" height="122" fill="var(--white)"/>
    <path d="M104,996 L98,1005 L104,1014" fill="none" stroke="#fff" stroke-width="2"/>
    <path d="M706,996 L712,1005 L706,1014" fill="none" stroke="#fff" stroke-width="2"/>
    <!-- footer -->
    <path d="M0,1130 C200,1112 420,1138 620,1126 C820,1114 950,1106 1039,1116 V1200 H0 Z" fill="url(#footerFill)"/>
  </svg>

  <div class="abs logo">LOGO</div>
  <div class="abs social" aria-label="Social links"><span></span><span></span><span></span></div>

  <div class="abs tagline">Reach Us to to Get a Great Environment<br>for tour in Your Lifetime Experience.</div>
  <div class="abs dots"><i class="on"></i><i></i><i></i></div>

  <nav class="abs nav">
    <a class="active" href="#" style="width:131px">Home</a>
    <a href="#" style="width:137px">About Us</a>
    <a href="#" style="width:132px">Find Job</a>
    <a href="#" style="width:167px">Register Here</a>
    <a href="#" style="width:146px">Contact Us</a>
  </nav>

  <h2 class="abs section-title welcome-title">Welcome to our site</h2>
  <div class="abs rule welcome-rule"></div>
  <div class="abs portrait" role="img" aria-label="Photo: businessman in a suit with folded hands"></div>
  <p class="abs intro">We need a design for the login page, about page, and inner pages of a recruitment site for an oil and gas company. Design should be modern, sleek, professional and colors can be blue, green, white, orange or any other recommended colors. We need a design for the login page, about page, and inner pages of a recruitment site for an oil and gas company.</p>
  <h3 class="abs theory-title">Our Unique Employee Developement Theory :</h3>
  <ul class="abs theory-list">
    <li><svg viewBox="0 0 14 12"><path d="M1,1 L5,3 L4,5 L13,11" stroke="#1a5c9c" stroke-width="2" fill="none"/></svg>Put here something you want to share with your Job Seekers.</li>
    <li><svg viewBox="0 0 14 12"><path d="M1,1 L5,3 L4,5 L13,11" stroke="#1a5c9c" stroke-width="2" fill="none"/></svg>Put here something you want to share with your Job Seekers.</li>
  </ul>

  <h2 class="abs section-title history-title">Our Employement History</h2>
  <div class="abs rule history-rule"></div>
  <div class="abs carousel-photo p1" role="img" aria-label="Photo: smiling professional woman"></div>
  <div class="abs carousel-photo p2" role="img" aria-label="Photo: engineering team in hard hats"></div>
  <div class="abs carousel-photo p3" role="img" aria-label="Photo: smiling professional woman"></div>
  <div class="abs carousel-photo p4" role="img" aria-label="Photo: engineering team in hard hats"></div>

  <div class="abs login-title">Login Here</div>
  <div class="abs field f1">User Name</div>
  <div class="abs field f2">Password</div>
  <div class="abs btn b1">Login</div>
  <div class="abs btn b2">Register Here</div>

  <h2 class="abs address-title">Company Address:</h2>
  <div class="abs rule address-rule"></div>
  <address class="abs address" style="font-style:normal">
    12/B, Harbor Crest Road, East Dale<br>
    Phone : 555 0142 3310/ 3318<br>
    Fax : 555 0142 3390/ 3394<br>
    Email : hello@rigcareers.example<br>
    SkyPe : rigcareers.hr
  </address>

  <div class="abs copyright">Copyright @ 2012, <u>Company Name</u></div>
  <div class="abs footer-nav"><span>Home</span><span>|</span><span>About Us</span><span>|</span><span>Find Job</span><span>|</span><span>Register Here</span><span>|</span><span>Contact Us</span></div>
</div>
</body>
</html>
```